Brightmill Data Works

Our company is about IT hardwares and IT solutions. IT hardware such as PC, RAMS, storage and servers. IT solutions such as project management, BA. We are also selling new technology too.

Target Market(s)

Consumer, Small to Medium Business, Corporate

Requirements
Must have
• The business card must have the following:
• Name:
• Title:
• Contact Number:
• Email address:
• Website:
• Color: Must match the logo color upgrade

```html
<!DOCTYPE html>
<html lang="en">
<head>
<meta charset="UTF-8">
<title>Brightmill Data Works – Business Card</title>
<link rel="stylesheet" href="https://fonts.googleapis.com/css2?family=Jura:wght@500;700&family=Michroma&display=swap">
<style>
  :root {
    --page-bg: #d9d3ca;
    --card-bg: #f3f2f1;
    --card-edge: #dcdad8;
    --ink: #2f2f31;
    --ink-soft: #4a4a4c;
    --accent: #b0612a;
    --corner-light: #c6a27a;
    --corner-dark: #a9705a;
    --icon-fg: #ffffff;
  }
  * { margin: 0; padding: 0; box-sizing: border-box; }
  html, body {
    width: 1200px; height: 970px; overflow: hidden;
    background: var(--page-bg);
  }
  .canvas {
    position: relative; width: 1200px; height: 970px;
  }
  .card {
    position: absolute; left: 100px; top: 205px;
    width: 1000px; height: 560px;
    background: var(--card-bg);
    border: 2px solid var(--card-edge);
    border-radius: 26px;
    overflow: hidden;
    box-shadow: 0 18px 40px rgba(60, 45, 30, 0.18);
  }
  .card__corner {
    position: absolute; left: 0; top: 0;
    width: 540px; height: 320px;
  }
  .brand {
    position: absolute; left: 60px; top: 255px; width: 420px;
    text-align: center;
  }
  .brand__dot {
    display: block; margin: 0 auto 26px;
    width: 56px; height: 56px; border-radius: 50%;
    background: var(--accent);
  }
  .brand__name {
    font-family: "Jura", sans-serif; font-weight: 700;
    font-size: 46px; line-height: 1.05; letter-spacing: 1px;
    color: var(--ink-soft); text-transform: uppercase;
  }
  .person {
    position: absolute; right: 82px; top: 78px; text-align: right;
    font-family: "Michroma", sans-serif;
  }
  .person__name { font-size: 32px; font-weight: 400; color: var(--ink); letter-spacing: 1px; }
  .person__title { font-size: 26px; color: var(--accent); margin-top: 8px; }
  .contacts {
    position: absolute; right: 82px; top: 370px;
    list-style: none; font-family: "Jura", sans-serif; font-weight: 500;
    font-size: 27px; color: var(--ink);
  }
  .contacts__item {
    display: flex; justify-content: flex-end; align-items: center;
    gap: 10px; height: 38px; letter-spacing: 0.5px;
  }
  .contacts__icon {
    width: 30px; height: 30px; background: var(--accent);
    display: flex; align-items: center; justify-content: center;
    flex-shrink: 0;
  }
  .contacts__icon svg { width: 22px; height: 22px; }
</style>
</head>
<body>
<main class="canvas">
  <section class="card">
    <svg class="card__corner" viewBox="0 0 540 320" role="img" aria-label="Decorative curved corner band in warm tan and brown tones">
      <defs>
        <linearGradient id="corner-fill" x1="0" y1="0" x2="1" y2="1">
          <stop offset="0" stop-color="var(--corner-light)"/>
          <stop offset="1" stop-color="var(--corner-dark)"/>
        </linearGradient>
      </defs>
      <path d="M0 0 H540 C380 40 150 150 0 320 Z" fill="url(#corner-fill)"/>
    </svg>

    <div class="brand">
      <span class="brand__dot"></span>
      <p class="brand__name">Brightmill<br>Data Works</p>
    </div>

    <div class="person">
      <h1 class="person__name">ALEX MARLOW</h1>
      <p class="person__title">MANAGER</p>
    </div>

    <ul class="contacts">
      <li class="contacts__item">+1-555-014-2290
        <span class="contacts__icon">
          <svg viewBox="0 0 24 24" aria-hidden="true"><path fill="var(--icon-fg)" d="M7 3l3 4-2 2c1 2.5 3.5 5 6 6l2-2 4 3-2 4C11 19 5 13 4 5z"/></svg>
        </span>
      </li>
      <li class="contacts__item">alex@brightmilldata.com
        <span class="contacts__icon">
          <svg viewBox="0 0 24 24" aria-hidden="true"><rect x="3" y="6" width="18" height="12" fill="none" stroke="var(--icon-fg)" stroke-width="2"/><path d="M3 6l9 7 9-7M3 18l7-6M21 18l-7-6" fill="none" stroke="var(--icon-fg)" stroke-width="2"/></svg>
        </span>
      </li>
      <li class="contacts__item">www.brightmilldata.com
        <span class="contacts__icon">
          <svg viewBox="0 0 24 24" aria-hidden="true"><g fill="none" stroke="var(--icon-fg)" stroke-width="1.6"><circle cx="12" cy="12" r="8.5"/><ellipse cx="12" cy="12" rx="4" ry="8.5"/><path d="M3.5 12h17M5 8h14M5 16h14"/></g></svg>
        </span>
      </li>
    </ul>
  </section>
</main>
</body>
</html>
```